Corvane Freight Company Business Card Design

We are a company that delivers natural saltwater (from the ocean) to aquarium companies, restaurants and home marine tanks. I would like a new business card to suit.

Must include Name, company name, abn, contact number and website as well as logo (see attached).

Looking for a design that stands out, has a clean but unique appearance.

Double and single sided entries welcome

Business

• Logo

```html
<!DOCTYPE html>
<html lang="en">
<head>
<meta charset="utf-8">
<title>Corvane Freight Company Business Cards</title>
<link rel="stylesheet" href="https://fonts.googleapis.com/css2?family=Source+Sans+3:wght@400;700&display=swap">
<style>
  :root {
    --stage: #161616;
    --card: #ffffff;
    --brand-blue: #1590d4;
    --ink-blue: #0c5ea8;
    --sky: #55c8f2;
    --deep: #0c63b3;
    --grey: #6b6b6b;
    --rule: #b9b9b9;
  }
  * { box-sizing: border-box; margin: 0; padding: 0; }
  html, body {
    width: 1200px; height: 750px; overflow: hidden;
    background: var(--stage);
    font-family: "Source Sans 3", "Myriad Pro", Arial, sans-serif;
  }
  .canvas { position: relative; width: 1200px; height: 750px; }

  .card {
    position: absolute;
    background: var(--card);
    width: 516px; height: 295px;
  }
  .card--front-light { left: 74px; top: 64px; }
  .card--front-deep { left: 607px; top: 64px; }
  .card--back { left: 342px; top: 400px; }

  .tab {
    position: absolute; top: 104px;
    width: 8px; height: 88px;
    background: var(--sky);
  }
  .tab--left { left: -2px; border-radius: 0 3px 3px 0; }
  .tab--right { right: -2px; border-radius: 3px 0 0 3px; }
  .card--front-deep .tab { background: var(--deep); }

  .wordmark {
    position: absolute;
    color: var(--brand-blue);
    font-weight: 400;
    white-space: nowrap;
    letter-spacing: -0.5px;
    line-height: 1;
  }
  .card--front-light .wordmark,
  .card--front-deep .wordmark {
    left: 22px; top: 132px; font-size: 31px;
  }
  .card--back .wordmark {
    left: 0; right: 0; top: 122px;
    text-align: center; font-size: 56px;
  }

  .divider {
    position: absolute; left: 272px; top: 62px;
    width: 2px; height: 174px;
    background: linear-gradient(to bottom, rgba(185,185,185,0), var(--rule) 20%, var(--rule) 80%, rgba(185,185,185,0));
  }

  .details { position: absolute; left: 290px; top: 64px; color: var(--ink-blue); }
  .details__name { font-size: 19px; font-weight: 700; line-height: 24px; }
  .details__title { font-size: 14.5px; color: var(--grey); line-height: 20px; margin-bottom: 6px; }
  .contact { list-style: none; font-size: 13px; line-height: 18.5px; }
  .contact li { display: flex; align-items: center; gap: 6px; }
  .contact svg { width: 11px; height: 11px; flex: none; }
  .address { font-size: 13px; line-height: 19px; margin-top: 20px; }
</style>
</head>
<body>
<main class="canvas">

  <section class="card card--front-light">
    <span class="tab tab--left"></span>
    <span class="tab tab--right"></span>
    <div class="wordmark">Corvane Freight</div>
    <span class="divider"></span>
    <div class="details">
      <p class="details__name">Your Name</p>
      <p class="details__title">Title</p>
      <ul class="contact">
        <li>
          <svg viewBox="0 0 12 12" aria-hidden="true"><path d="M3 1.2 4.6 3.4 3.6 4.6c.6 1.5 1.8 2.7 3.3 3.3l1.2-1 2.2 1.6-.9 1.9C5.6 10.2 1.8 6.4 1.2 2.1z" fill="none" stroke="currentColor" stroke-width="1"/></svg>
          123-456-7892
        </li>
        <li>
          <svg viewBox="0 0 12 12" aria-hidden="true"><g fill="none" stroke="currentColor" stroke-width="1"><circle cx="6" cy="6" r="4.8"/><ellipse cx="6" cy="6" rx="2" ry="4.8"/><path d="M1.2 6h9.6"/></g></svg>
          www.corvanefreight.com
        </li>
      </ul>
      <p class="address">Street Name, City Name ,<br>State, Zip Code<br>ABN: 123456789</p>
    </div>
  </section>

  <section class="card card--front-deep">
    <span class="tab tab--left"></span>
    <span class="tab tab--right"></span>
    <div class="wordmark">Corvane Freight</div>
    <span class="divider"></span>
    <div class="details">
      <p class="details__name">Your Name</p>
      <p class="details__title">Title</p>
      <ul class="contact">
        <li>
          <svg viewBox="0 0 12 12" aria-hidden="true"><path d="M3 1.2 4.6 3.4 3.6 4.6c.6 1.5 1.8 2.7 3.3 3.3l1.2-1 2.2 1.6-.9 1.9C5.6 10.2 1.8 6.4 1.2 2.1z" fill="none" stroke="currentColor" stroke-width="1"/></svg>
          123-456-7892
        </li>
        <li>
          <svg viewBox="0 0 12 12" aria-hidden="true"><g fill="none" stroke="currentColor" stroke-width="1"><circle cx="6" cy="6" r="4.8"/><ellipse cx="6" cy="6" rx="2" ry="4.8"/><path d="M1.2 6h9.6"/></g></svg>
          www.corvanefreight.com
        </li>
      </ul>
      <p class="address">Street Name, City Name ,<br>State, Zip Code<br>ABN: 123456789</p>
    </div>
  </section>

  <section class="card card--back">
    <div class="wordmark">Corvane Freight</div>
  </section>

</main>
</body>
</html>
```